Velmori Sciences needs high end Label Design for a revolutionary new supplement

We at Velmori Sciences are looking for a brand new Label Design for a first of its kind product called Solvenna. It is the first supplement on the market that treats grief and heartbreak. This product is unisex for both men and woman. We want the New Label to look high end and luxurious using the brand colors which are gold and burgundy. Please feel free to use other colors such as black, white, or gray to go along with it or any other colors if you feel would be a great fit! Velmori Sciences is like the Tarnwick of the supplement world, coming out with new products that will challenge the way people treat different symptoms. To Recap:

1. Product Name: SOLVENNA - the font will play a big roll
2. The Label will be placed on an all white bottle
3. Some parts of the label will be printed with foil to make parts of the label shiny and more attractive. Please keep this in mind when designing.
4. Must use our Logo. I will attach a file of our logo and of the emblem as well. Feel free to use the emblem separately if you have a great idea for it. Please let us know if you need the Logo in a different file type.
5. This all natural herbal supplement in pill form is the first to treat grief and support someone with a broken heart. The consumers purchasing this product will be going through a hard and emotional time. This is a serious product.
6. The manufacturer has included some basic instructions regarding the dye line and file types. Please do your best to meet these. If you cannot meet the guidelines please submit art work anyways. If your design is chosen we will just have the manufacturer replicate the design.

The final label should portray Solvenna and Velmori Sciences as a luxurious brand and product which was made with cutting edge science leading the way with revolutionary ideas. We want customers to feel that the product is worth every penny, because it is. As soon as they receive the product and take one look at the label, I want them to think WOW I made the right choice buying this. I have attached some Label designs that we really liked for your review.

Please feel free to message me with any questions or if you need the Logo in a different file type. Thank you all.
Updates

Please send in more entries while we take a couple days to review, we are still looking for that one design we can work with. We are getting close, thank you all!

Target Market(s)

People going through grief and heartbreak.

Font styles to use
Sans Serif
Script
Other font styles liked:
• Any font that looks good, The font for the name SOLVENNA is very important and will brand it. We hated the font used in the label we received in our first label draft (attached so you can see)

Requirements
Must have
• Must have the company Logo that says the company name
• Must have the colors Gold and Burgundy
• Must have some areas that will be the shiny foil when label is printed.
• Must say "Dietary Supplement" somewhere near the bottom along with "90 Capsules"
• I have attached a Label someone designed for us but were not really happy with. I did like the font the "Dietary supplement" and "90 Capsules" had and also where it was placed. We absolutely HATED the font used for Solvenna.
• Must look at the label design we received from the manufacturer and take into consideration the room needed to write in the directions and all the symbols such as "made in america" and "KMT Facility" Don't worry about adding these in as they will put those in before printing but keep in mind they will be added to the Final Label along with the Supplement Facts.
Nice to have
• Would like to see other colors to go with gold and burgundy suck as black, white, or gray. I have attached some Label designs that I really liked for your reference.
Should not have
• Does not need to have any other legal language, that will be applied by the the manufacturer's graphics team.

```html
<!DOCTYPE html>
<html lang="en">
<head>
<meta charset="utf-8">
<title>Solvenna – Label</title>
<link href="https://fonts.googleapis.com/css2?family=Anton&family=Arimo:wght@400;700&family=Cinzel:wght@600&family=Open+Sans:ital,wght@0,400;0,600;0,700;1,700&display=swap" rel="stylesheet">
<style>
  :root {
    --burgundy: #7a1519;
    --burgundy-deep: #5a0d10;
    --gold: #c9a24a;
    --gold-light: #e6c574;
    --cream: #dcbf7a;
    --ink: #1d1d1d;
    --white: #ffffff;
    --backdrop: #e7e7e8;
  }
  * { margin: 0; padding: 0; box-sizing: border-box; }
  html, body { width: 954px; height: 1200px; overflow: hidden; }
  body { background: var(--backdrop); position: relative; font-family: "Open Sans", sans-serif; }

  .label {
    position: absolute; left: 27px; top: 420px;
    width: 900px; height: 361px;
    background: var(--burgundy);
    box-shadow: 0 6px 18px rgba(0,0,0,.25);
    overflow: hidden;
  }
  .label-shapes { position: absolute; inset: 0; }

  /* left info panel */
  .info { position: absolute; left: 20px; top: 38px; width: 215px; color: var(--cream); font-size: 7.4px; line-height: 1.2; }
  .info p { margin-bottom: 7px; }
  .info b { font-weight: 700; }
  .info .caps { text-transform: uppercase; }

  .badges { position: absolute; left: 22px; top: 208px; display: flex; gap: 10px; }
  .badge { width: 36px; display: flex; flex-direction: column; align-items: center; gap: 4px; }
  .badge-mark { width: 34px; height: 34px; border-radius: 50%; border: 2px solid var(--gold); background: rgba(201,162,74,.12); }
  .badge span { font-size: 7px; color: var(--cream); white-space: nowrap; }

  .dates { position: absolute; left: 168px; top: 280px; color: var(--cream); font-size: 9.5px; line-height: 1.35; }

  /* centre */
  .brand { position: absolute; left: 340px; top: 42px; width: 220px; text-align: center; }
  .brand-dot { width: 40px; height: 40px; border-radius: 50%; background: var(--burgundy); margin: 0 auto 12px; }
  .brand-name { font-family: "Cinzel", serif; font-weight: 600; color: var(--burgundy); font-size: 24px; letter-spacing: 3px; line-height: 1; }
  .brand-name.second { font-size: 20px; letter-spacing: 4px; margin-top: 2px; }

  .product-name {
    position: absolute; left: 300px; top: 168px; width: 300px; text-align: center;
    font-family: "Anton", sans-serif; font-size: 62px; line-height: 1; letter-spacing: 1px;
    color: var(--burgundy);
    text-shadow: 2px 2px 0 var(--burgundy-deep);
  }
  .product-type {
    position: absolute; left: 370px; top: 252px; width: 160px; text-align: center;
    font-style: italic; font-weight: 700; font-size: 17px; line-height: 1.25; color: var(--ink);
  }
  .count {
    position: absolute; left: 308px; top: 260px; width: 80px; height: 80px; border-radius: 50%;
    background: var(--burgundy); border: 4px solid var(--gold);
    display: flex; flex-direction: column; align-items: center; justify-content: center;
    color: var(--gold-light); line-height: 1;
  }
  .count-number { font-size: 28px; font-weight: 600; }
  .count-unit { font-size: 15px; font-weight: 600; }

  /* supplement facts */
  .facts { position: absolute; left: 643px; top: 37px; width: 253px; border: 1.5px solid var(--ink); padding: 3px 5px 2px; font-family: "Arimo", sans-serif; color: var(--ink); background: var(--white); }
  .facts-title { font-weight: 700; font-size: 22px; line-height: 1; letter-spacing: .3px; }
  .facts-size { font-size: 11.5px; padding-bottom: 3px; border-bottom: 6px solid var(--ink); }
  .facts-head { display: flex; justify-content: space-between; font-size: 10.5px; font-weight: 700; padding: 2px 0; border-bottom: 3px solid var(--ink); }
  .facts-row { display: flex; font-size: 10px; padding: 3px 0; border-bottom: 1px solid var(--ink); }
  .facts-row .n { flex: 1; }
  .facts-row .a { width: 50px; }
  .facts-row .d { width: 14px; text-align: right; }
  .facts-row.last { border-bottom: 3px solid var(--ink); }
  .facts-note { font-size: 9.5px; padding-top: 2px; }
  .ingredients { position: absolute; left: 643px; top: 206px; width: 255px; font-family: "Arimo", sans-serif; font-size: 9.4px; line-height: 1.3; color: var(--ink); }
  .ingredients p + p { margin-top: 3px; }

  .distributor { position: absolute; left: 645px; top: 302px; color: var(--gold); font-weight: 700; font-size: 16.5px; line-height: 1.3; }
</style>
</head>
<body>
<main class="label">
  <svg class="label-shapes" viewBox="0 0 900 361" width="900" height="361" aria-hidden="true">
    <defs>
      <linearGradient id="foil" x1="0" y1="0" x2="1" y2="0">
        <stop offset="0" stop-color="#a9802f"/>
        <stop offset=".45" stop-color="#f0d48a"/>
        <stop offset="1" stop-color="#b38a38"/>
      </linearGradient>
      <linearGradient id="panel" x1="0" y1="0" x2="0" y2="1">
        <stop offset="0" stop-color="#7e171b"/>
        <stop offset="1" stop-color="#5f0e11"/>
      </linearGradient>
    </defs>
    <rect width="900" height="361" fill="url(#panel)"/>
    <rect width="900" height="22" fill="url(#foil)"/>
    <path d="M332,22 L900,22 L900,262 C800,268 620,290 500,330 C460,345 430,355 410,361 C330,345 272,280 276,180 C280,100 305,55 332,22 Z" fill="#fff"/>
    <path d="M332,22 C305,55 280,100 276,180 C272,280 330,345 410,361" fill="none" stroke="url(#foil)" stroke-width="6"/>
    <path d="M900,262 C800,268 620,290 500,330 C460,345 430,355 410,361" fill="none" stroke="url(#foil)" stroke-width="6"/>
  </svg>

  <section class="info">
    <p><b>Direction:</b> Adult take 2 Capsules daily, as a dietary supplement. Or as directed by a health practitioner</p>
    <p><b>Benefits:</b> Promote fat burning, help to control the weight.</p>
    <p><b>Warnings:</b> If you are pregnant or breastfeeding, persons under the age of 18, consult a doctor before use. Do not use if you are hypersensitivity to any of the formula ingredients.</p>
    <p><b>Storage Condition:</b> Keep container tightly sealed in a cool and dry place. Avoide heat and light.</p>
    <p class="caps"><b>Precautions:</b><br>Do not use this product if safety seal is missing or broken keep out of reach of children.</p>
  </section>

  <ul class="badges" style="list-style:none">
    <li class="badge"><div class="badge-mark"></div><span>Cruelty Free</span></li>
    <li class="badge"><div class="badge-mark"></div><span>Sugar Free</span></li>
    <li class="badge"><div class="badge-mark"></div><span>Dairy Free</span></li>
    <li class="badge"><div class="badge-mark"></div><span>Gluten Free</span></li>
    <li class="badge"><div class="badge-mark"></div><span>Non GMO</span></li>
  </ul>

  <div class="dates">Manufacturing:<br>00 / 00 /00<br>Expiry date:<br>00 / 00 /00</div>

  <div class="brand">
    <div class="brand-dot"></div>
    <div class="brand-name">VELMORI</div>
    <div class="brand-name second">SCIENCES</div>
  </div>

  <h1 class="product-name">SOLVENNA</h1>
  <div class="product-type">DIETARY<br>SUPPLEMENT</div>

  <div class="count"><span class="count-number">90</span><span class="count-unit">Capsules</span></div>

  <section class="facts">
    <div class="facts-title">Supplement Facts</div>
    <div class="facts-size">Serving Size 1 Capsule</div>
    <div class="facts-head"><span>Amount Per Serving</span><span>% DV</span></div>
    <div class="facts-row"><span class="n">Milk Thistle Seed Extract<br>&nbsp;&nbsp;&nbsp;standardized to 80% silymarin<br>(140 mg)</span><span class="a">175 mg</span><span class="d">**</span></div>
    <div class="facts-row last"><span class="n">Blessed Thistle (stem. leaf, Flower)</span><span class="a">120 mg</span><span class="d">**</span></div>
    <div class="facts-note">**Daily Value (DV) not established.</div>
  </section>
  <div class="ingredients">
    <p>Other Ingredients: plant-derived capsule (hypromellose), Cellulose</p>
    <p>GLUTEN-FREE, SUGAR-FREE, NO PRESERVATIVES ADDED, NO ARTIFICIAL FLAVOR</p>
  </div>

  <div class="distributor">Distributed by:<br>Velmori Sciences, LLC</div>
</main>
</body>
</html>
```